Venture Capital firm needs modern business cards

We are a Venture Capital firm within financial services/Asset management. The industry generally has basic business cards with black, blue and maybe green/yellow design elements.
Our firm has a four-colour swoosh logo. We are based in London and want to stand out, just a little bit!, from the crowd. Our company is called LORV Investments and the 'C' stands for collaboration thus using makerswarm is a natural portal for our business card design competition. Our logo came via makerswarm too!
We use 'Venture Partner in Asset Management' as our tagline and this is Trademark registered. We operate in a conservative industry and we should not overstep our mark. The logo is colorful as it is and therefore the rest of the design should not be too fanciful.
The objective is twofold: make our logo element stick and memorable with our audience, whilst representing a conservative yet young image.
Updates
The Business Card obviously needs a field for Name, Surname, Job Title, Adress fields: Street, City, Postcode, Country, telefone and cell number, website address, etc.
We have uploaded the ai file. We trust that these are OK. If not, please advise.
Reason: We have have been busy with a client engagement. We will set the project as Guaranteed in return for the troubles we cause. Apologies for the confusion.
Thank you all for these great and creative design suggestions. The team is very happy with a number of your ideas! We will be in touch tomorrow to give individual feedback before the project closes on Friday. We look forward to working with some of you to narrow down your creations. Thank you, LORV Investments team.
All,
Target Market(s)
Financial Services Professionals, Investors, Media, 35-70 years, mainly male, well educated
Industry/Entity Type
Conservative
Requirements
Must have
- We must make use of our logo and potential tagline 'Venture Partner in Asset Management' as we are establishing a new Brand and new company in the market.
We can use 'LORV', 'LORV Investments', and 'LORV Investments'+tagline 'Venture Partner in Asset Management' or simply the four-colour swoosh plus the name of the company as part of the text. (see files)
All design elements are available in black or grey-scale if required. (grey scale swoosh attached).
Due to regulation we must have the following wording on the card in small print 'LORV Investments is an Appointed Representative of Bramwell Holdings Partnership Limited, which is authorised by the Monetary Oversight Board'.
Nice to have
- We would consider designs that make use of different printing techniques such embossing/debossing, UV spot etc.
We attach our colour palette in the files section for your reference.
Should not have
- The font we use for our company name is 'EXO' so do not use a font style that clashes with the corporate fonts, please.
Do not use other design elements than the ones we provide in the file library as part of this project.

```html
<!DOCTYPE html>
<html lang="en">
<head>
<meta charset="utf-8">
<title>LORV Investments – Business Card Presentation</title>
<link href="https://fonts.googleapis.com/css2?family=Arimo:wght@400;700&display=swap" rel="stylesheet">
<style>
  :root {
    --board: #e4e5e7;
    --card-white: #f0f1f3;
    --card-grey: #77787b;
    --card-yellow: #fcd20a;
    --card-teal: #86cdd3;
    --ink-dark: #58595b;
    --ink-light: #ffffff;
    --die-cut: #e6e7e9;
    --note-ink: #111111;
    --shadow: 0 3px 5px rgba(0,0,0,0.22), 0 1px 2px rgba(0,0,0,0.15);
  }
  html, body {
    margin: 0;
    width: 1200px;
    height: 800px;
    overflow: hidden;
    background: var(--board);
    font-family: "Arimo", Arial, sans-serif;
  }
  .board { position: relative; width: 1200px; height: 800px; }
  .card {
    position: absolute;
    border-radius: 12px;
    box-shadow: var(--shadow);
    overflow: hidden;
  }
  .card svg { display: block; width: 100%; height: 100%; }
  .card--front { background: var(--card-white); }
  .card--grey { background: var(--card-grey); }
  .card--yellow { background: var(--card-yellow); }
  .card--teal { background: var(--card-teal); }

  .card--front-large { left: 258px; top: 243px; width: 435px; height: 248px; }
  .card--grey { left: 76px; top: 104px; width: 435px; height: 248px; transform: rotate(-29deg); }
  .card--front-small { left: 800px; top: 45px; width: 322px; height: 183px; }
  .card--yellow { left: 802px; top: 245px; width: 320px; height: 183px; }
  .card--front-bottom { left: 94px; top: 545px; width: 348px; height: 198px; }
  .card--teal { left: 474px; top: 545px; width: 350px; height: 200px; }

  .wordmark { font-family: "Arimo", Arial, sans-serif; font-weight: 400; fill: var(--ink-dark); }
  .tagline { font-family: "Arimo", Arial, sans-serif; fill: var(--ink-dark); }
  .mark-circle { fill: var(--ink-dark); opacity: 0.35; }
  .back-text { font-family: "Arimo", Arial, sans-serif; fill: var(--ink-light); }
  .back-name { font-weight: 700; }
  .icon { fill: none; stroke: var(--ink-light); stroke-width: 0.9; stroke-linejoin: round; stroke-linecap: round; }
  .die-cut { fill: var(--die-cut); }

  .note {
    position: absolute;
    left: 808px; top: 482px;
    margin: 0;
    font-size: 13px;
    color: var(--note-ink);
  }
</style>
</head>
<body>
<main class="board">

  <svg width="0" height="0" style="position:absolute" aria-hidden="true">
    <defs>
      <symbol id="card-front" viewBox="0 0 348 198">
        <circle class="mark-circle" cx="46" cy="145" r="28"/>
        <text class="wordmark" x="80" y="170" font-size="80" letter-spacing="-1">lorv</text>
        <text class="tagline" x="83" y="182" font-size="7">Venture Partner in Asset Management</text>
      </symbol>
      <symbol id="card-back" viewBox="0 0 350 200">
        <text class="back-text back-name" x="334" y="69" font-size="12.5" text-anchor="end">Martin Hale</text>
        <text class="back-text" x="318" y="82" font-size="10" text-anchor="end">Chairman</text>
        <g class="back-text" font-size="10" text-anchor="end">
          <text x="195" y="67">martin@lorvinvestments.com</text>
          <text x="195" y="85">www.lorvinvestments.com</text>
          <text x="195" y="103">+1 (800) 555-0142</text>
          <text x="195" y="122">+1 (800) 555-0142</text>
          <text x="195" y="137">12 Harrow Lane, 7 Marlow Square,</text>
          <text x="195" y="150">London, United Kingdom EC4N 2QP</text>
        </g>
        <g class="icon">
          <rect x="207" y="59" width="11" height="8"/>
          <path d="M207 59 l5.5 4.5 l5.5 -4.5"/>
          <circle cx="212.5" cy="82" r="5"/>
          <path d="M207.5 82 h10 M212.5 77 c-3 3 -3 7 0 10 c3 -3 3 -7 0 -10"/>
          <path d="M208 96 c0 5 4 9 9 9 l1 -2 l-2.5 -2 l-1.5 1 c-1.5 -1 -3 -2.5 -4 -4 l1 -1.5 l-2 -2.5 z"/>
          <rect x="209" y="113" width="7" height="11" rx="1"/>
          <path d="M211.5 122 h2"/>
          <path d="M207 142 l5.5 -5 l5.5 5 M208.5 141 v6 h8 v-6 M211 147 v-3 h3 v3"/>
        </g>
        <circle class="die-cut" cx="299" cy="148" r="27" role="img" aria-label="Die-cut brand mark area"/>
      </symbol>
    </defs>
  </svg>

  <article class="card card--front card--front-large" aria-label="Card front">
    <svg viewBox="0 0 348 198"><use href="#card-front"/></svg>
  </article>

  <article class="card card--grey" aria-label="Card back, grey">
    <svg viewBox="0 0 350 200"><use href="#card-back"/></svg>
  </article>

  <article class="card card--front card--front-small" aria-label="Card front">
    <svg viewBox="0 0 348 198"><use href="#card-front"/></svg>
  </article>

  <article class="card card--yellow" aria-label="Card back, yellow">
    <svg viewBox="0 0 350 200"><use href="#card-back"/></svg>
  </article>

  <article class="card card--front card--front-bottom" aria-label="Card front">
    <svg viewBox="0 0 348 198"><use href="#card-front"/></svg>
  </article>

  <article class="card card--teal" aria-label="Card back, teal">
    <svg viewBox="0 0 350 200"><use href="#card-back"/></svg>
  </article>

  <p class="note">• Note : Three colour options,&nbsp; swoosh is die cut.</p>

</main>
</body>
</html>
```